Quillfern Vaults - Direct Mailer / Flyer

We are excited to announce the launch of our new company, Quillfern Vaults, a premier cohosting facility and data center dedicated to Cryptocurrency Miners. Our website, https://quillfernvaults.example, provides detailed information about our offerings and showcases the innovative design schemes for the entire project.

Quillfern Vaults stands out in the industry by offering both GPU Hosting and ASIC Hosting services in our state-of-the-art facility, equipped with an impressive 17 Megawatts of available power. What sets us apart is our unique billing system based on actual metered power usage. We charge $0.08 for ASIC miners and $0.09 for GPU miners, ensuring cost-effectiveness and transparency for our clients.

Our commitment to excellence is evident in our use of cutting-edge technology, top-notch facilities, and strategic partnerships. These elements come together to deliver exceptional solutions tailored for real-world applications in the cryptocurrency space.

As part of our promotional efforts, we are developing a direct mailer/flyer to introduce Quillfern Vaults to a wider audience. This promotional material will also serve as a handout at events, to potential customers, and more. We welcome creative ideas and suggestions to maximize the versatility of this design and reach diverse target audiences effectively.

For a comprehensive overview of our services and to explore our design concepts, please visit https://quillfernvaults.example. Quillfern Vaults is poised to revolutionize the mining industry, and we look forward to partnering with you for success in the digital currency era.

```html
<!DOCTYPE html>
<html lang="en">
<head>
<meta charset="utf-8">
<title>Quillfern Vaults – Flyer</title>
<link href="https://fonts.googleapis.com/css2?family=Oswald:wght@400;500;700&family=Roboto:wght@400&display=swap" rel="stylesheet">
<style>
  :root {
    --page-bg: #d3d3d3;
    --sheet-bg: #f4f5f7;
    --ink: #1c1c1c;
    --body-grey: #555a60;
    --brand-blue: #3553fa;
    --stat-bg: #e6eaf8;
    --card-bg: #ffffff;
    --white: #ffffff;
  }
  * { box-sizing: border-box; margin: 0; padding: 0; }
  html, body { width: 1200px; height: 1200px; overflow: hidden; }
  body { background: var(--page-bg); position: relative; font-family: "Roboto", sans-serif; }

  .flyer {
    position: absolute; left: 200px; top: 40px;
    width: 800px; height: 1120px;
    background: var(--sheet-bg);
    overflow: hidden;
    box-shadow: 0 10px 30px rgba(0,0,0,0.18);
  }
  .hero-art { position: absolute; left: 0; top: 0; width: 800px; height: 1120px; }

  .brand {
    position: absolute; left: 41px; top: 31px;
    display: flex; align-items: center; gap: 9px;
    font-family: "Oswald", sans-serif; font-weight: 700;
    font-size: 27px; line-height: 27px; color: var(--ink);
    letter-spacing: 0.5px; text-transform: uppercase;
  }
  .brand-square { width: 27px; height: 25px; background: var(--ink); }

  .hero-title {
    position: absolute; left: 71px; top: 192px;
    font-family: "Oswald", sans-serif; font-weight: 700;
    font-size: 33px; line-height: 36px; color: var(--white);
    text-transform: uppercase; letter-spacing: 0.3px;
  }
  .hero-sub {
    position: absolute; left: 72px; top: 277px; width: 340px;
    font-family: "Oswald", sans-serif; font-weight: 400;
    font-size: 20.5px; line-height: 23px; color: var(--white);
    text-transform: uppercase; white-space: nowrap;
  }

  .call {
    position: absolute; left: 519px; top: 404px;
    display: flex; align-items: center; gap: 12px;
    color: var(--white); font-family: "Oswald", sans-serif;
  }
  .call-icon { width: 52px; height: 52px; border-radius: 50%; background: var(--white);
    display: flex; align-items: center; justify-content: center; }
  .call-label { font-size: 12px; line-height: 14px; font-weight: 400; }
  .call-number { font-size: 24px; line-height: 30px; font-weight: 500; letter-spacing: 0.3px; }

  .section-title {
    position: absolute; top: 540px;
    font-family: "Oswald", sans-serif; font-weight: 700;
    font-size: 31px; line-height: 40px; color: var(--ink); text-transform: uppercase;
  }
  .who-title { left: 53px; }
  .what-title { left: 436px; }

  .who-lead {
    position: absolute; left: 52px; top: 596px;
    font-family: "Oswald", sans-serif; font-weight: 400;
    font-size: 19.5px; line-height: 26px; color: var(--ink); text-transform: uppercase;
  }
  .who-body {
    position: absolute; left: 53px; top: 632px; width: 337px;
    font-size: 16px; line-height: 26px; color: var(--body-grey);
    text-align: justify;
  }

  .stat {
    position: absolute; top: 777px; width: 151px; height: 98px;
    background: var(--stat-bg); border-radius: 14px;
    padding: 17px 0 0 18px; color: var(--brand-blue);
  }
  .stat-power { left: 55px; }
  .stat-green { left: 225px; }
  .stat-value { font-family: "Oswald", sans-serif; font-weight: 700; font-size: 20px; line-height: 26px; }
  .stat-label { font-size: 13px; line-height: 16px; margin-top: 3px; }

  .coin-photo { position: absolute; left: 55px; top: 895px; width: 336px; height: 175px; }

  .service {
    position: absolute; left: 439px; width: 324px; height: 103px;
    background: var(--card-bg); box-shadow: 0 2px 6px rgba(0,0,0,0.05);
  }
  .service::before {
    content: ""; position: absolute; left: 1px; top: 19px; width: 4px; height: 18px;
    background: var(--brand-blue);
  }
  .service-title {
    position: absolute; left: 23px; top: 16px;
    font-family: "Oswald", sans-serif; font-weight: 700; font-size: 15px; line-height: 22px;
    color: var(--brand-blue); text-transform: uppercase;
  }
  .service-text {
    position: absolute; left: 23px; top: 49px; width: 276px;
    font-size: 12.4px; line-height: 16px; color: var(--body-grey); text-align: justify;
  }
  .service-gpu { top: 600px; }
  .service-asic { top: 723px; }
  .service-hardware { top: 845px; }
  .service-consulting { top: 967px; }
</style>
</head>
<body>
<main class="flyer">
  <svg class="hero-art" viewBox="0 0 800 1120" width="800" height="1120">
    <defs>
      <linearGradient id="heroBand" x1="0" y1="0" x2="0" y2="1">
        <stop offset="0" stop-color="#5a5a5a"/>
        <stop offset="0.45" stop-color="#3a3a3a"/>
        <stop offset="1" stop-color="#111111"/>
      </linearGradient>
      <radialGradient id="mineScene" cx="0.7" cy="0.55" r="0.75">
        <stop offset="0" stop-color="#c8682a"/>
        <stop offset="0.45" stop-color="#6b3a1e"/>
        <stop offset="1" stop-color="#1e1a18"/>
      </radialGradient>
      <radialGradient id="coinScene" cx="0.38" cy="0.55" r="0.7">
        <stop offset="0" stop-color="#e6a440"/>
        <stop offset="0.5" stop-color="#7a4a1a"/>
        <stop offset="1" stop-color="#121016"/>
      </radialGradient>
    </defs>
    <polygon class="hero-band" points="0,108 402,108 491,378 473,444 0,444" fill="url(#heroBand)"
      role="img" aria-label="Dark blurred background of stacked coins"/>
    <polygon class="hero-photo" points="442,0 800,0 800,378 491,378 402,108" fill="url(#mineScene)"
      role="img" aria-label="Miners in hard hats working beside a large copper coin in a glowing foundry"/>
    <polygon class="call-band" points="497,378 800,378 800,483 455,483" fill="var(--brand-blue)"/>
    <polygon class="corner-band" points="0,1032 270,1032 305,1120 0,1120" fill="var(--brand-blue)"/>
  </svg>

  <div class="brand"><span class="brand-square"></span>Quillfern Vaults</div>

  <h1 class="hero-title">Transform Mining<br>with Cohosting</h1>
  <p class="hero-sub">Miners deserve the best - choose<br>the hosting company that delivers<br>excellence!</p>

  <div class="call">
    <div class="call-icon">
      <svg width="24" height="24" viewBox="0 0 24 24" aria-hidden="true">
        <path d="M6.6 10.8a15.1 15.1 0 0 0 6.6 6.6l2.2-2.2c.3-.3.7-.4 1-.2 1.1.4 2.3.6 3.6.6.6 0 1 .4 1 1V20c0 .6-.4 1-1 1A17 17 0 0 1 3 4c0-.6.4-1 1-1h3.5c.6 0 1 .4 1 1 0 1.3.2 2.5.6 3.6.1.3 0 .7-.2 1z" fill="var(--brand-blue)"/>
      </svg>
    </div>
    <div>
      <div class="call-label">Call Us :</div>
      <div class="call-number">+1 555 014 2760</div>
    </div>
  </div>

  <h2 class="section-title who-title">Who We Are</h2>
  <h2 class="section-title what-title">What We Do</h2>

  <p class="who-lead">Real solutions for real applications</p>
  <p class="who-body">Quillfern Vaults has committed to leveraging cutting-edge technology, state-of-the-art facilities, and strategic partnerships to deliver exceptional solutions tailored for real-world applications in the cryptocurrency space.</p>

  <div class="stat stat-power">
    <div class="stat-value">17,000,000+</div>
    <div class="stat-label">watts available for hosting</div>
  </div>
  <div class="stat stat-green">
    <div class="stat-value">2,000,000+</div>
    <div class="stat-label">watts of green energy being produced</div>
  </div>

  <svg class="coin-photo" viewBox="0 0 336 175" width="336" height="175">
    <rect width="336" height="175" fill="url(#coinScene)" role="img"
      aria-label="Gold coins lying in front of a trading candlestick chart"/>
  </svg>

  <article class="service service-gpu">
    <h3 class="service-title">GPU Hosting</h3>
    <p class="service-text">Begin your GPU Hosting journey with rates starting at $0.09 kWh, accepting all equipment.</p>
  </article>
  <article class="service service-asic">
    <h3 class="service-title">ASIC Hosting</h3>
    <p class="service-text">Get your ASICs directly from us or send yours in today, starting at an all-in rate of $0.08 kWh.</p>
  </article>
  <article class="service service-hardware">
    <h3 class="service-title">Mining Hardware</h3>
    <p class="service-text">Looking for mining hardware? Our equipment comes with no additional markup, ever.</p>
  </article>
  <article class="service service-consulting">
    <h3 class="service-title">Crypto Consulting</h3>
    <p class="service-text">Enjoy complete White Glove Services for setup, insurance, and tax consulting.</p>
  </article>
</main>
</body>
</html>
```